Rollers & Glides.com

Vertical Business Card with focus on branding with our icon. Information on card will be logo, persons name, position, phone number, email address and website. Use the the name Marcus Pellow, position President, phone number 480.915.2267, email Marcus@rollersandglides-demo.com, website www.rollersandglides-demo.com.

```html
<!DOCTYPE html>
<html lang="en">
<head>
<meta charset="utf-8">
<title>Rollers &amp; Glides.com — Business Card</title>
<link rel="stylesheet" href="https://fonts.googleapis.com/css2?family=Arimo:wght@400;700&family=Rubik:wght@500&display=swap">
<style>
  :root {
    --brand-blue: #325fae;
    --brand-blue-light: #4570b8;
    --card-white: #ffffff;
    --tint: #e9eef6;
    --ink: #1e1e1e;
    --backdrop: #b9b9b9;
  }
  * { margin: 0; padding: 0; box-sizing: border-box; }
  html, body {
    width: 1200px; height: 900px; overflow: hidden;
    background: var(--backdrop);
  }
  .stage { position: relative; width: 1200px; height: 900px; }
  .card {
    position: absolute; width: 560px; height: 320px;
    border-radius: 26px; overflow: hidden;
    box-shadow: 0 6px 14px rgba(0,0,0,.35);
  }
  .card--front { left: 60px; top: 120px; background: var(--brand-blue); }
  .card--back { left: 580px; top: 460px; background: var(--card-white); }

  .decor-circle {
    position: absolute; border-radius: 50%;
  }
  .card--front .decor-circle {
    width: 300px; height: 300px; right: -60px; top: -40px;
    border: 44px solid var(--brand-blue-light);
  }
  .card--back .decor-circle {
    width: 320px; height: 320px; right: -70px; top: -60px;
    border: 46px solid var(--tint);
  }

  .front-brand {
    position: absolute; left: 0; right: 0; top: 90px;
    display: flex; flex-direction: column; align-items: center; gap: 22px;
  }
  .brand-dot {
    width: 58px; height: 58px; border-radius: 50%;
    border: 12px solid var(--card-white);
  }
  .front-brand .brand-name {
    font-family: "Rubik", sans-serif; font-weight: 500;
    font-size: 30px; letter-spacing: 3px; color: var(--card-white);
  }

  .back-brand {
    position: absolute; left: 40px; top: 42px;
    display: flex; align-items: center; gap: 16px;
  }
  .back-brand .brand-dot {
    width: 36px; height: 36px; border-width: 8px; border-color: var(--brand-blue);
  }
  .back-brand .brand-name {
    font-family: "Rubik", sans-serif; font-weight: 500;
    font-size: 22px; letter-spacing: 2px; color: var(--brand-blue);
  }

  .person { position: absolute; left: 60px; top: 150px; font-family: "Arimo", sans-serif; }
  .person-name {
    font-weight: 700; font-size: 22px; color: var(--brand-blue);
    text-transform: uppercase; letter-spacing: .5px;
  }
  .person-role { font-size: 15px; color: var(--ink); margin-top: 2px; }

  .contacts {
    position: absolute; left: 60px; top: 222px; list-style: none;
    font-family: "Arimo", sans-serif; font-size: 14px; color: var(--ink);
  }
  .contacts li { display: flex; align-items: center; gap: 10px; height: 22px; }
  .contacts svg { width: 14px; height: 14px; flex: none; }
  .contacts .accent { color: var(--brand-blue); }
</style>
</head>
<body>
<main class="stage">

  <section class="card card--front" aria-label="Card front">
    <div class="decor-circle"></div>
    <div class="front-brand">
      <span class="brand-dot"></span>
      <span class="brand-name">Rollers &amp; Glides.com</span>
    </div>
  </section>

  <section class="card card--back" aria-label="Card back">
    <div class="decor-circle"></div>
    <div class="back-brand">
      <span class="brand-dot"></span>
      <span class="brand-name">Rollers &amp; Glides.com</span>
    </div>

    <div class="person">
      <p class="person-name">Marcus Pellow</p>
      <p class="person-role">President</p>
    </div>

    <ul class="contacts">
      <li>
        <svg viewBox="0 0 24 24" fill="#325fae" aria-hidden="true"><path d="M6.6 10.8a15.1 15.1 0 0 0 6.6 6.6l2.2-2.2a1 1 0 0 1 1-.25 11.4 11.4 0 0 0 3.6.57 1 1 0 0 1 1 1V20a1 1 0 0 1-1 1A17 17 0 0 1 3 4a1 1 0 0 1 1-1h3.5a1 1 0 0 1 1 1c0 1.25.2 2.45.57 3.57a1 1 0 0 1-.25 1z"/></svg>
        <span>480.915.2267</span>
      </li>
      <li>
        <svg viewBox="0 0 24 24" aria-hidden="true"><rect x="2" y="5" width="20" height="14" fill="#325fae"/><path d="M2 5l10 8 10-8" fill="none" stroke="#fff" stroke-width="2"/></svg>
        <span>Marcus@rollersandglides-demo.com</span>
      </li>
      <li>
        <svg viewBox="0 0 24 24" fill="none" stroke="#325fae" stroke-width="2" aria-hidden="true"><circle cx="12" cy="12" r="10"/><ellipse cx="12" cy="12" rx="4" ry="10"/><path d="M2 12h20M4 7h16M4 17h16"/></svg>
        <span>www.<span class="accent">rollersandglides-demo</span>.com</span>
      </li>
    </ul>
  </section>

</main>
</body>
</html>
```